Band and Coaching business card (creative industry)

My company The Fenwick Ensemble is the name of my band Soul outfit but is also a brand I use for my coaching business which is Performance coaching in the following areas: Corporate coaching, acting, vocals and dialect. The band plays for corporate events and private functions as well as local bar/restaurant/festivals.
Updates

Hi All

Please see updated info for the wording of the business card front and back.  This is ito then be followed with contact number, email and facebook link

first side should have:

JulieRose Brannigan
Creative Director
( followed by contact info as per previous)

Side 2:

The Fenwick Ensemble  - Band  
 Vocalist      I   Musician    I  Songwriter

The Fenwick Ensemble  - Studio
Performance Coaching  
Acting  I  Vocals  I Dialect  I Corporate Coaching

Industry/Entity Type

Events

Contact Information for Business Card

The Fenwick Ensemble (logo)
JulieRose Brannigan
Musician/Vocalist/Performance Coach
M: 0412 605 918
E: thefenwickensemble@mailbrook.net
W: www.friendspace.net/thefenwickensembleband

Font styles to use
Sans Serif

Requirements
Must have
• first side should have:

JulieRose Brannigan
Creative Director

Side 2:

The Fenwick Ensemble - Band
Vocalist I Musician I Songwriter

The Fenwick Ensemble - Studio
Performance Coaching
Acting I Vocals I Dialect I Corporate Coaching
Nice to have
• I like smaller business cards with curved edges.

some ideas for look in additional business cards attached.
Should not have
• music notes or anything specific to the field. Want to keep it funky and contemporary

```html
<!DOCTYPE html>
<html lang="en">
<head>
<meta charset="utf-8">
<title>JulieRose Brannigan — Business Card</title>
<link rel="stylesheet" href="https://fonts.googleapis.com/css2?family=Open+Sans:wght@400&family=Sofia+Sans+Extra+Condensed:wght@600&display=swap">
<style>
  :root {
    --magenta: #c413e2;
    --magenta-deep: #b80fdc;
    --violet: #7b1ef2;
    --orchid: #b31fe0;
    --contact: #a31fe2;
    --paper: #fbfbfc;
    --white: #ffffff;
  }
  html, body {
    margin: 0;
    padding: 0;
    overflow: hidden;
    background: var(--paper);
  }
  .card {
    position: relative;
    width: 1200px;
    height: 741px;
    overflow: hidden;
    background: var(--paper);
    font-family: "Open Sans", sans-serif;
  }
  .card__side-band {
    position: absolute;
    inset: 0;
    width: 1200px;
    height: 741px;
  }
  .brand-badge {
    position: absolute;
    left: 144px;
    top: 273px;
    width: 226px;
    height: 226px;
    border-radius: 50%;
    background: linear-gradient(90deg, #e21ad6 0%, var(--violet) 100%);
    display: flex;
    align-items: center;
    justify-content: center;
    text-align: center;
  }
  .brand-badge__name {
    color: var(--white);
    font-family: "Open Sans", sans-serif;
    font-weight: 400;
    font-size: 25px;
    line-height: 1.2;
    margin: 0;
  }
  .identity {
    position: absolute;
    right: 160px;
    top: 212px;
    text-align: right;
  }
  .identity__name {
    margin: 0;
    font-family: "Sofia Sans Extra Condensed", sans-serif;
    font-weight: 600;
    font-size: 92px;
    line-height: 1;
    color: var(--violet);
    letter-spacing: 4.5px;
    margin-right: -4.5px;
  }
  .identity__role {
    margin: 4px 0 0;
    font-size: 27px;
    color: var(--orchid);
  }
  .contacts {
    position: absolute;
    left: 443px;
    top: 443px;
    height: 177px;
    margin: 0;
    list-style: none;
    border-left: 3px solid var(--magenta-deep);
    padding-left: 30px;
    box-sizing: border-box;
    display: flex;
    flex-direction: column;
    justify-content: center;
    gap: 20px;
  }
  .contacts__item {
    display: flex;
    align-items: center;
    gap: 8px;
    font-size: 24px;
    color: var(--contact);
    line-height: 1;
    height: 32px;
  }
  .contacts__icon {
    width: 24px;
    height: 24px;
    fill: var(--magenta-deep);
    flex: none;
  }
</style>
</head>
<body>
  <main class="card">
    <svg class="card__side-band" viewBox="0 0 1200 741" aria-hidden="true">
      <path d="M0 0 H378 C262 150 200 330 228 500 C248 612 308 690 357 741 H0 Z" fill="var(--magenta)"/>
    </svg>

    <div class="brand-badge">
      <p class="brand-badge__name">The Fenwick<br>Ensemble</p>
    </div>

    <header class="identity">
      <h1 class="identity__name">JulieRose Brannigan</h1>
      <p class="identity__role">Creative Director</p>
    </header>

    <ul class="contacts">
      <li class="contacts__item">
        <svg class="contacts__icon" viewBox="0 0 24 24" aria-hidden="true">
          <path d="M6.6 2.5c.6-.3 1.3-.1 1.6.5l1.8 3.6c.3.6.1 1.2-.4 1.6L8.2 9.3c.9 2.5 2.2 4.6 3.9 6.3l1.6-.9c.5-.3 1.2-.2 1.6.3l2.5 3.1c.4.5.3 1.3-.2 1.7l-1.5 1.2c-1 .8-2.4.9-3.5.2C7.9 18.2 4.9 12.6 4.6 6.3c0-1.2.6-2.3 1.6-2.9z"/>
        </svg>
        <span>:0412 605 918</span>
      </li>
      <li class="contacts__item">
        <svg class="contacts__icon" viewBox="0 0 24 24" aria-hidden="true">
          <path d="M1 5h22v14H1z" fill="var(--magenta-deep)"/>
          <path d="M2.5 6.5 12 13l9.5-6.5" fill="none" stroke="var(--paper)" stroke-width="1.6"/>
        </svg>
        <span>:thefenwickensemble@mailbrook.net</span>
      </li>
      <li class="contacts__item">
        <svg class="contacts__icon" viewBox="0 0 24 24" aria-hidden="true">
          <g fill="none" stroke="var(--magenta-deep)" stroke-width="2">
            <circle cx="12" cy="12" r="9.5"/>
            <ellipse cx="12" cy="12" rx="4.2" ry="9.5"/>
            <path d="M2.5 12h19"/>
          </g>
        </svg>
        <span>:www.friendspace.net/thefenwickensembleband</span>
      </li>
    </ul>
  </main>
</body>
</html>
```